Corporate Business Card

Very professional, Modern, Not to busy, include phone address email, website
(253) 617-4930, 18761 52nd Avenue S, Kent, WA 98047, martin@plumlinegroup.com, varkoworks.com

Target Market(s)

Manufacturing

Industry/Entity Type

Aero, machining, manufacturing, Off road racing

Contact Information for Business Card

Phone, address email, website

```html
<!DOCTYPE html>
<html lang="en">
<head>
<meta charset="utf-8">
<title>Varko Works – Business Card</title>
<link rel="stylesheet" href="https://fonts.googleapis.com/css2?family=Arimo:wght@400;700&display=swap">
<style>
  :root {
    --backdrop: #e6e6e4;
    --card: #363636;
    --card-dark: #2b2b2b;
    --pattern-light: #4a4a4a;
    --white: #ffffff;
    --red: #c8171c;
    --rule: #d9d9d9;
  }
  * { margin: 0; padding: 0; box-sizing: border-box; }
  html, body {
    width: 1200px; height: 801px; overflow: hidden;
    background: var(--backdrop);
    font-family: "Arimo", Arial, sans-serif;
  }
  .canvas { position: relative; width: 1200px; height: 801px; }

  .card {
    position: absolute;
    top: 246px;
    width: 525px; height: 300px;
    background: var(--card);
    overflow: hidden;
  }
  .card--front { left: 50px; }
  .card--back { left: 625px; }

  /* Front */
  .brand-name {
    position: absolute; left: 40px; top: 52px;
    color: var(--white);
    font-weight: 700; font-size: 46px; letter-spacing: 1px;
    line-height: 1;
  }
  .brand-rule {
    position: absolute; left: 40px; top: 118px;
    width: 200px; height: 2px; background: var(--rule);
  }
  .person { position: absolute; left: 40px; top: 148px; }
  .person__name {
    color: var(--red); font-size: 19px; letter-spacing: 0.5px;
    text-transform: uppercase;
  }
  .person__title { color: var(--white); font-size: 15px; margin-top: 4px; text-align: right; }
  .divider {
    position: absolute; left: 262px; top: 120px;
    width: 1px; height: 82px; background: var(--rule);
  }
  .contacts { position: absolute; left: 282px; top: 124px; list-style: none; }
  .contacts li {
    display: flex; align-items: center; gap: 9px;
    color: var(--white); font-size: 13.5px; margin-bottom: 9px;
  }
  .contacts svg { width: 14px; height: 14px; flex: none; }
  .address {
    position: absolute; left: 40px; bottom: 40px;
    color: var(--white); font-size: 15px; letter-spacing: 0.3px;
  }

  /* Back */
  .back-texture {
    position: absolute; inset: 0;
    background: linear-gradient(135deg, var(--card-dark) 0%, var(--pattern-light) 55%, var(--card-dark) 100%);
  }
  .back-brand {
    position: absolute; left: 50%; top: 50%;
    transform: translate(-50%, -50%);
    display: flex; align-items: center; gap: 8px;
    color: var(--white); font-weight: 700; font-size: 22px; letter-spacing: 0.5px;
  }
  .back-brand__mark { width: 10px; height: 10px; background: var(--red); }
</style>
</head>
<body>
<main class="canvas">

  <section class="card card--front" aria-label="Business card front">
    <div class="brand-name">VARKO WORKS</div>
    <div class="brand-rule"></div>

    <div class="person">
      <p class="person__name">Daniel Reyes</p>
      <p class="person__title">Manager</p>
    </div>

    <div class="divider"></div>

    <ul class="contacts">
      <li>
        <svg viewBox="0 0 16 16" aria-hidden="true"><circle cx="8" cy="8" r="8" fill="var(--red)"/><path d="M5 4.5l1.5-.5 1 2-1 .8a5 5 0 0 0 2.7 2.7l.8-1 2 1-.5 1.5c-3.5.3-6.8-3-6.5-6.5z" fill="#fff"/></svg>
        (253) 617-4930
      </li>
      <li>
        <svg viewBox="0 0 16 16" aria-hidden="true"><rect x="1" y="3.5" width="14" height="9" fill="var(--red)"/><path d="M1 3.5l7 5 7-5" fill="none" stroke="#fff" stroke-width="1.2"/></svg>
        martin@plumlinegroup.com
      </li>
      <li>
        <svg viewBox="0 0 16 16" aria-hidden="true"><circle cx="8" cy="8" r="7" fill="var(--red)"/><path d="M1 8h14M8 1c-3 3.5-3 10.5 0 14M8 1c3 3.5 3 10.5 0 14" fill="none" stroke="#fff" stroke-width="1"/></svg>
        www.varkoworks.com
      </li>
    </ul>

    <p class="address">18761 52nd Avenue S, Kent, WA 98047</p>
  </section>

  <section class="card card--back" aria-label="Business card back">
    <div class="back-texture" role="img" aria-label="Embossed repeating brand-name texture in dark grey tones"></div>
    <div class="back-brand">
      <span class="back-brand__mark"></span>
      VARKO WORKS
    </div>
  </section>

</main>
</body>
</html>
```